Need Business Card for eLearning Company

Need a business card designed for our company, CareerVantly.

CareerVantly has developed a complete 12 lesson eLearning course to teach you the skills you need to present yourself in a job interview. The course uses advanced learning techniques in the multimedia videos, plus contains quizzes and additional exercises to insure you get the course and can walk into any interview with confidence and ease, and get the job.

www.careervantly-example.com

Industry/Entity Type

Business

```html
<!DOCTYPE html>
<html lang="en">
<head>
<meta charset="utf-8">
<title>CareerVantly Business Card</title>
<link rel="stylesheet" href="https://fonts.googleapis.com/css2?family=Didact+Gothic&family=Montserrat:wght@600&display=swap">
<style>
  :root {
    --canvas: #2b2a2b;
    --card-white: #ffffff;
    --card-dark: #403d3e;
    --ink: #3a3a3a;
    --ink-soft: #6a6a6a;
    --rule: #b9b9b9;
    --green: #8cc21f;
    --purple: #8e1f7d;
    --on-dark: #ffffff;
  }
  * { box-sizing: border-box; margin: 0; padding: 0; }
  html, body { width: 1200px; height: 675px; overflow: hidden; }
  body {
    background: var(--canvas);
    font-family: "Didact Gothic", sans-serif;
    position: relative;
  }
  .card {
    position: absolute;
    top: 189px;
    width: 520px;
    height: 297px;
    overflow: hidden;
  }
  .card--front { left: 50px; background: var(--card-white); color: var(--ink); }
  .card--back { left: 630px; background: var(--card-dark); color: var(--on-dark); }

  /* brand name with plain dot */
  .brand { position: absolute; display: flex; align-items: center; gap: 12px; }
  .brand__dot { width: 30px; height: 30px; border-radius: 50%; flex: none; }
  .brand__name { font-size: 36px; line-height: 1; letter-spacing: 0.5px; }
  .slogan {
    position: absolute; font-size: 9px; letter-spacing: 1.4px; text-transform: uppercase;
  }
  .card--front .brand { left: 26px; top: 92px; }
  .card--front .brand__dot { background: var(--purple); }
  .card--front .brand__name { color: var(--ink); }
  .card--front .slogan { left: 68px; top: 140px; color: var(--ink-soft); }

  /* contact person */
  .person { position: absolute; right: 24px; top: 50px; text-align: right; }
  .person__name { font-family: "Montserrat", sans-serif; font-weight: 600; font-size: 13px; color: var(--green); }
  .person__role { font-size: 10px; color: var(--ink-soft); padding-bottom: 4px; border-bottom: 2px solid var(--purple); width: 148px; margin-left: auto; }
  .address { position: absolute; right: 24px; top: 104px; text-align: right; font-size: 10.5px; line-height: 1.35; color: var(--ink); }

  /* rule and accent band */
  .divider { position: absolute; left: 20px; top: 190px; width: 300px; height: 1px; background: var(--rule); }
  .accent { position: absolute; right: 0; top: 178px; width: 210px; height: 26px; }

  /* contacts */
  .contacts { position: absolute; left: 22px; top: 210px; list-style: none; font-size: 11.5px; line-height: 1.55; color: var(--ink); }
  .contacts li { display: flex; align-items: center; gap: 8px; }
  .contacts svg { width: 11px; height: 11px; fill: var(--green); flex: none; }

  /* back side */
  .card--back .brand { left: 50%; top: 96px; transform: translateX(-50%); }
  .card--back .brand__dot { background: var(--on-dark); }
  .card--back .brand__name { color: var(--on-dark); }
  .card--back .slogan { left: 0; right: 0; top: 142px; text-align: center; color: var(--on-dark); }
  .website { position: absolute; left: 0; right: 0; top: 182px; text-align: center; font-family: "Montserrat", sans-serif; font-weight: 600; font-size: 12px; letter-spacing: 0.3px; }
</style>
</head>
<body>
  <section class="card card--front" aria-label="Business card front">
    <div class="brand">
      <span class="brand__dot"></span>
      <span class="brand__name">CareerVantly</span>
    </div>
    <p class="slogan">Interview skills online</p>

    <div class="person">
      <p class="person__name">Daniel Okafor</p>
      <p class="person__role">Principal</p>
    </div>
    <p class="address">418 Linden Avenue<br>Riverton, IL 60999</p>

    <div class="divider"></div>
    <svg class="accent" viewBox="0 0 210 26" preserveAspectRatio="none" aria-hidden="true">
      <polygon points="0,26 40,0 40,26" fill="#403d3e"/>
      <polygon points="40,0 210,0 210,26 40,26" fill="#8cc21f"/>
    </svg>

    <ul class="contacts">
      <li>
        <svg viewBox="0 0 12 12" aria-hidden="true"><path d="M1 4c0-1.5 2-2.5 5-2.5S11 2.5 11 4v1H8.5V4h-5v1H1zM2.5 6h7l1 4.5h-9z"/></svg>
        555.210.4837
      </li>
      <li>
        <svg viewBox="0 0 12 12" aria-hidden="true"><path d="M3 1h6v3H3zM1 5h10v5H9V8H3v2H1zM3.5 9h5v2.5h-5z"/></svg>
        555.306.9142
      </li>
      <li>
        <svg viewBox="0 0 12 12" aria-hidden="true"><path d="M1 2.5h10v7H1zM1.6 3.2 6 6.8l4.4-3.6"/></svg>
        daniel@careervantly-example.com
      </li>
    </ul>
  </section>

  <section class="card card--back" aria-label="Business card back">
    <div class="brand">
      <span class="brand__dot"></span>
      <span class="brand__name">CareerVantly</span>
    </div>
    <p class="slogan">Interview skills online</p>
    <p class="website">www.careervantly-example.com</p>
  </section>
</body>
</html>
```